plumbers buisness card

A buisness card for a plumbing buisness
needs to have a water theme with navy blue, light blue and white
with an image of either a water drop, pipes, tools or something relating to plumbing and incorperating my buisness name as a logo

"Kettering Plumbing" is the words that need to stand out with "& gasfitting" to be smaller

spelling error on brief, "maintenance"
and also could you include my email d_kettering@mailwave.com.au

Industry/Entity Type

Plumbing

Contact Information for Business Card

Kettering Plumbing & Gasfitting

declan kettering
0432961085

specialising in
-new homes
-maitenance
-renovations

license no.
-73840

```html
<!DOCTYPE html>
<html lang="en">
<head>
<meta charset="utf-8">
<title>Kettering Plumbing &amp; Gasfitting – Business Card</title>
<link href="https://fonts.googleapis.com/css2?family=PT+Sans:wght@400;700&family=PT+Sans+Narrow:wght@700&family=Arimo&display=swap" rel="stylesheet">
<style>
  :root {
    --stage: #c9b15a;
    --card-blue: #35639b;
    --tap-light: #7fb0e6;
    --tap-mid: #4f86c6;
    --tap-deep: #2f5f9e;
    --accent-orange: #f07a12;
    --ink-white: #ffffff;
    --label-ink: #1a1a1a;
  }
  * { margin: 0; padding: 0; box-sizing: border-box; }
  html, body { width: 1200px; height: 434px; overflow: hidden; }
  body { background: var(--stage); position: relative; font-family: "PT Sans", sans-serif; color: var(--ink-white); }

  .side-label {
    position: absolute; top: 34px; width: 300px;
    font-family: "Arimo", sans-serif; font-size: 37px; color: var(--label-ink);
    text-align: center; line-height: 1;
  }
  .side-label--front { left: 150px; }
  .side-label--back { left: 777px; }

  .card {
    position: absolute; top: 92px; width: 533px; height: 305px;
    background: var(--card-blue); overflow: hidden;
  }
  .card--front { left: 40px; }
  .card--back { left: 623px; width: 534px; }

  .card__art { position: absolute; inset: 0; width: 100%; height: 100%; }

  .card__text { position: absolute; top: 0; height: 100%; text-align: center; }
  .card--front .card__text { left: 235px; width: 280px; }
  .card--back .card__text { left: 250px; width: 284px; }

  .line { position: absolute; left: 0; right: 0; white-space: nowrap; line-height: 1; }

  .contact-name { top: 27px; font-weight: 700; font-size: 19px; }
  .contact-phone { top: 54px; font-size: 17px; }
  .brand-name { top: 110px; font-family: "PT Sans Narrow", sans-serif; font-weight: 700; font-size: 42px; }
  .brand-trade { top: 160px; font-family: "PT Sans Narrow", sans-serif; font-weight: 700; font-size: 34px; }
  .brand-amp { top: 212px; font-family: "PT Sans Narrow", sans-serif; font-weight: 700; font-size: 23px; }
  .brand-sub { top: 246px; font-family: "PT Sans Narrow", sans-serif; font-weight: 700; font-size: 26px; }

  .services-title {
    top: 86px; font-weight: 700; font-size: 15px;
  }
  .services-title span { display: inline-block; padding: 0 4px 4px; border-bottom: 1px solid var(--ink-white); }
  .service { font-size: 14px; }
  .service--homes { top: 120px; }
  .service--maintenance { top: 141px; }
  .service--renovations { top: 162px; }
  .detail { font-size: 14px; }
  .detail--email { top: 197px; }
  .detail--license { top: 215px; }
</style>
</head>
<body>
  <div class="side-label side-label--front">Front</div>
  <div class="side-label side-label--back">Back</div>

  <section class="card card--front">
    <svg class="card__art" viewBox="0 0 533 305" preserveAspectRatio="none">
      <defs>
        <linearGradient id="tapFront" x1="0" y1="0" x2="1" y2="1">
          <stop offset="0" stop-color="var(--tap-light)"/>
          <stop offset="0.5" stop-color="var(--tap-mid)"/>
          <stop offset="1" stop-color="var(--tap-deep)"/>
        </linearGradient>
      </defs>
      <path role="img" aria-label="Photo of a chrome water tap with running water" d="M0 0 H175 Q250 150 235 305 H0 Z" fill="url(#tapFront)"/>
      <path d="M175 0 Q250 150 235 305" fill="none" stroke="var(--accent-orange)" stroke-width="3"/>
    </svg>
    <div class="card__text">
      <div class="line contact-name">Declan Kettering</div>
      <div class="line contact-phone">0432961085</div>
      <div class="line brand-name">KETTERING</div>
      <div class="line brand-trade">Plumbing</div>
      <div class="line brand-amp">&amp;</div>
      <div class="line brand-sub">gasfitting</div>
    </div>
  </section>

  <section class="card card--back">
    <svg class="card__art" viewBox="0 0 534 305" preserveAspectRatio="none">
      <defs>
        <linearGradient id="tapBack" x1="0" y1="0" x2="1" y2="1">
          <stop offset="0" stop-color="var(--tap-light)"/>
          <stop offset="0.5" stop-color="var(--tap-mid)"/>
          <stop offset="1" stop-color="var(--tap-deep)"/>
        </linearGradient>
      </defs>
      <path role="img" aria-label="Photo of a chrome water tap with running water" d="M0 0 H175 Q250 150 235 305 H0 Z" fill="url(#tapBack)"/>
      <path d="M175 0 Q250 150 235 305" fill="none" stroke="var(--accent-orange)" stroke-width="3"/>
    </svg>
    <div class="card__text">
      <div class="line services-title"><span>Specialising in :</span></div>
      <div class="line service service--homes">new homes</div>
      <div class="line service service--maintenance">maintenance</div>
      <div class="line service service--renovations">renovations</div>
      <div class="line detail detail--email">e-mail :&nbsp; d_kettering@mailwave.com.au</div>
      <div class="line detail detail--license">license no. 73840</div>
    </div>
  </section>
</body>
</html>
```